New Website Design for PHOVAN.org

We are looking for a new website design for PHOVAN.org. PHOVAN is a non profit home inspector association based in California. Home Inspectors are people that come out and look at a house before it's purchased to let the buyer know of any defects that may exist.
Our site is based on Joomla so if you'll be able to make a Joomla 3 template as well, please let us know (not required, but a bonus).
We would like to see designs that incorporate royal blue, white and chrome into the site as that's our main business colors.
We would like a place for rotating banners though they don't need to be the same size as the current site.
We would like navigation to be easier to manage with menus only across the top (via drop down menus) where we are going to sort out the items currently on the side. Possibly the front page could have a graphic link to separate portals for Realtors, Home Buyers and Inspectors, but that's just one option.
We would like a good mobile design or something that will scale easily to mobile.
The Find an Inspector feature is important and should stand out. The ASK PHOVANr site
Current home page feels a bit busy. Would like to simplify a bit.

```html
<!DOCTYPE html>
<html lang="en">
<head>
<meta charset="utf-8">
<title>PHOVAN — Pacific Home Valuation and Inspection Network</title>
<link href="https://fonts.googleapis.com/css2?family=Ropa+Sans&family=Open+Sans:wght@400;600&display=swap" rel="stylesheet">
<style>
:root{
  --page:#ececec;
  --white:#ffffff;
  --royal:#2b3d8f;
  --royal-dark:#1f2d6e;
  --ink:#222;
  --muted:#8a8a8a;
  --link:#3a8fd1;
  --rule:#e2e2e2;
  --black:#050505;
}
*{box-sizing:border-box;margin:0;padding:0}
html,body{width:917px;height:1200px;overflow:hidden;background:var(--page)}
body{position:relative;font-family:"Open Sans",sans-serif;color:var(--ink)}
.abs{position:absolute}
.display{font-family:"Ropa Sans",sans-serif}

/* header */
.brand-dot{left:96px;top:15px;width:76px;height:76px;border-radius:50%;background:var(--royal)}
.brand-name{left:186px;top:33px;font-family:"Ropa Sans",sans-serif;font-size:19px;line-height:23px;color:#1d1d1d}
.account{right:126px;top:5px;font-size:11.5px;color:#333;font-family:"Ropa Sans",sans-serif}
.account span{margin:0 6px}
.support-icon{left:660px;top:44px}
.support{left:705px;top:46px;font-family:"Ropa Sans",sans-serif}
.support .label{font-size:12px;color:var(--royal)}
.support .phone{font-size:15.5px;color:#222;margin-top:1px;letter-spacing:.3px}

/* nav */
.nav{left:84px;top:107px;width:749px;height:35px;background:var(--royal)}
.nav a{position:absolute;top:0;line-height:35px;font-family:"Ropa Sans",sans-serif;font-size:12px;color:var(--white);text-decoration:none}
.nav .current{left:0;width:67px;background:var(--white);color:#222;text-align:center}

/* hero */
.hero{left:84px;top:142px;width:749px;height:310px;background:linear-gradient(100deg,#a8a89a 0%,#6f7a5a 28%,#9aa08c 50%,#7c8a64 72%,#5f7048 100%)}
.hero-caption{left:490px;top:308px;width:331px;height:133px;background:rgba(40,40,40,.78);padding:14px 15px;color:var(--white)}
.hero-caption .kicker{font-family:"Ropa Sans",sans-serif;font-size:21px;line-height:22px}
.hero-caption .headline{font-family:"Ropa Sans",sans-serif;font-size:26.5px;line-height:28px}
.hero-caption p{font-size:10.5px;line-height:14.5px;margin-top:9px;padding-left:4px}

/* intro */
.panel{left:84px;top:452px;width:749px;height:520px;background:var(--white)}
.intro{left:108px;top:472px;width:560px;font-size:12.3px;line-height:20px;color:#333}
.find-btn{left:674px;top:468px;width:134px;height:44px;border-radius:22px;background:linear-gradient(#4a62c4,#26399a 55%,#1c2c80);box-shadow:0 3px 3px rgba(0,0,0,.25),inset 0 1px 0 rgba(255,255,255,.35);color:var(--white);font-family:"Ropa Sans",sans-serif;font-size:13.5px;line-height:44px;text-align:center;letter-spacing:.3px}
.rule{left:84px;width:749px;height:1px;background:var(--rule)}

/* portals */
.portal-icon{left:108px}
.portal-title{left:175px;font-family:"Ropa Sans",sans-serif;font-size:16px;color:var(--royal)}
.portal-text{left:177px;width:162px;font-size:9.6px;line-height:15.5px;color:var(--muted)}
.portal-text a{color:var(--link);text-decoration:none}

/* welcome */
.welcome-title{left:359px;top:552px;font-family:"Ropa Sans",sans-serif;font-size:19.5px;line-height:26px;color:#222}
.welcome-text{left:359px;width:452px;font-size:9.6px;line-height:15.3px;color:var(--muted)}
.welcome-photo-frame{left:656px;top:668px;width:154px;height:92px;background:var(--white);border:1px solid #e4e4e4;padding:5px}
.welcome-photo{width:100%;height:100%;background:linear-gradient(135deg,#3c6fc9 0%,#6da0e6 55%,#d9d9d9 56%,#8c8c8c 100%)}

/* lists */
.list-title{top:818px;font-family:"Ropa Sans",sans-serif;font-size:14.5px;color:var(--royal)}
.list-item{font-size:9.6px;color:#777;line-height:12px}
.list-item small{display:block;font-size:8.3px;color:#888}
.news-thumb{left:588px;width:44px;height:40px;background:linear-gradient(#d8d2cc,#b5a593)}
.news-name{left:641px;font-size:9.6px;color:#333}
.news-text{left:641px;width:172px;font-size:8.6px;line-height:13px;color:var(--muted)}
.news-date{right:113px;font-size:7.8px;color:var(--royal)}

/* footer */
.footer{left:84px;top:972px;width:749px;height:174px;background:var(--royal);color:var(--white)}
.footer-title{top:993px;font-family:"Ropa Sans",sans-serif;font-size:15.5px;color:var(--white);text-shadow:0 1px 2px rgba(0,0,0,.45)}
.footer-text{font-size:9.6px;line-height:13px;color:#eef}
.footer-text.lines{line-height:16.8px}
.footer-text em{font-weight:600;font-style:italic}
.field{left:680px;width:142px;height:20px;background:linear-gradient(#fff,#e6e6e6);border-radius:3px;font-size:9px;color:#777;padding-left:6px;line-height:20px}
.login-btn{left:682px;top:1105px;width:52px;height:18px;background:linear-gradient(#fff,#e4e4e4);border-radius:2px;color:#222;font-size:9.6px;text-align:center;line-height:18px}
.bottom-bar{left:84px;top:1146px;width:749px;height:34px;background:var(--black);color:var(--white);font-size:10px;line-height:34px}
.bottom-bar .abs{top:0}
</style>
</head>
<body>

<!-- header -->
<div class="abs brand-dot"></div>
<div class="abs brand-name">Pacific Home Valuation<br>and Inspection Network</div>
<div class="abs account">Login<span>|</span>Register</div>
<svg class="abs support-icon" width="40" height="38" viewBox="0 0 40 38" aria-hidden="true">
  <path d="M6 22 A14 14 0 0 1 34 22" fill="none" stroke="#333" stroke-width="3"/>
  <rect x="3" y="19" width="8" height="13" rx="3" fill="#222"/>
  <rect x="29" y="19" width="8" height="13" rx="3" fill="#222"/>
  <path d="M8 32 Q12 37 20 36" fill="none" stroke="#333" stroke-width="2"/>
</svg>
<div class="abs support">
  <div class="label">24/7 Online Support</div>
  <div class="phone">1-300-555-0142</div>
</div>

<!-- navigation -->
<nav class="abs nav">
  <a class="current">Home</a>
  <a style="left:86px">Find an Inspector</a>
  <a style="left:211px">Home Buyers &amp; Sellers</a>
  <a style="left:362px">Real Estate Agents</a>
  <a style="left:492px">Inspectors</a>
  <a style="left:584px">Ask PHOVAN</a>
  <a style="left:673px">Conferences</a>
</nav>

<!-- hero -->
<div class="abs hero" role="img" aria-label="Photo of a home inspector pointing at a house siding while talking with a homeowner"></div>
<div class="abs hero-caption">
  <div class="kicker">The Leader in</div>
  <div class="headline">Home Inspection Service</div>
  <p>Le Lorem Ipsum est simplement du faux texte employé dans la composition et la mise en page avant impression. Le Lorem Ipsum est le faux.</p>
</div>

<!-- content panel -->
<div class="abs panel"></div>
<p class="abs intro">Le Lorem Ipsum est simplement du faux texte employé dans la composition et la mise en page avant impression.</p>
<div class="abs find-btn">FIND INSPECTOR</div>
<div class="abs rule" style="top:528px"></div>

<!-- portals -->
<svg class="abs portal-icon" style="top:552px" width="52" height="48" viewBox="0 0 52 48" aria-hidden="true">
  <path d="M2 20 L20 4 L38 20 Z" fill="#111"/>
  <rect x="2" y="20" width="3" height="26" fill="#111"/>
  <rect x="2" y="20" width="34" height="3" fill="#111"/>
  <circle cx="18" cy="34" r="6" fill="#111"/><circle cx="18" cy="34" r="2" fill="#fff"/>
  <rect x="23" y="32" width="24" height="4" fill="#111"/>
  <rect x="41" y="36" width="3" height="4" fill="#111"/>
</svg>
<div class="abs portal-title" style="top:555px">Home Buyers</div>
<p class="abs portal-text" style="top:578px">Le Lorem Ipsum est simplement du faux texte employé dans <a>More Info</a></p>

<svg class="abs portal-icon" style="top:632px" width="52" height="52" viewBox="0 0 52 52" aria-hidden="true">
  <path d="M2 20 L20 4 L38 20 Z" fill="#111"/>
  <rect x="2" y="20" width="3" height="28" fill="#111"/>
  <rect x="2" y="20" width="34" height="3" fill="#111"/>
  <circle cx="22" cy="36" r="7" fill="none" stroke="#111" stroke-width="3"/>
  <path d="M27 41 L38 48" stroke="#111" stroke-width="4"/>
</svg>
<div class="abs portal-title" style="top:634px">Home Inspectors</div>
<p class="abs portal-text" style="top:654px">Le Lorem Ipsum est simplement du faux texte employé dans <a>More Info</a></p>

<svg class="abs portal-icon" style="top:712px" width="52" height="54" viewBox="0 0 52 54" aria-hidden="true">
  <path d="M4 20 L24 3 L44 20 Z" fill="#111"/>
  <rect x="4" y="20" width="40" height="32" fill="#111"/>
  <rect x="12" y="30" width="28" height="16" fill="#fff"/>
  <text x="26" y="44" font-family="Open Sans,sans-serif" font-size="14" font-weight="600" text-anchor="middle" fill="#111">$</text>
</svg>
<div class="abs portal-title" style="top:714px">Home Realtors</div>
<p class="abs portal-text" style="top:734px">Le Lorem Ipsum est simplement du faux texte employé dans <a>More Info</a></p>

<!-- welcome -->
<h1 class="abs welcome-title" style="font-weight:400">Welcome to<br>Pacific Home Valuation and Inspection Network</h1>
<p class="abs welcome-text" style="top:613px">Lorem ipsum dolor sit amet, consectetuer adipiscing elit, sed diam nonummy nibh euismod ncidunt ut laoreet dolore magna aliquam erat volutpat. Ut wisi enim ad minim veniam., quis nostrud exerci tation ullamcorper suscipit lobortis nisl ut aliquip ex ea commodo consequat. Autem vel eum iriure dolor in hendrerit in vulputate velit esse molestie equat.</p>
<p class="abs welcome-text" style="top:682px;width:292px">Lacerat facer possim assum, Typi non habent claritatem insitst usus legentis in iis qui facit eorum claritatem. Investigationes verunt lectores legere me lius quod ii legunt saepius. Claritas processus dynamicus, qui sequitur mutationem. consuetudium lectorum. Mirum est notare quam littera gothica,</p>
<div class="abs welcome-photo-frame"><div class="welcome-photo" role="img" aria-label="Photo of an inspector on a ladder checking a roofline"></div></div>
<div class="abs rule" style="top:795px"></div>

<!-- press / events / news -->
<div class="abs list-title" style="left:110px">Press Achive</div>
<div class="abs list-item" style="left:110px;top:846px">Praesent luptatum delenit augue duis dolore<small>Yesterday at 08:23:14 PM</small></div>
<div class="abs list-item" style="left:110px;top:878px">Praesent luptatum delenit augue duis dolore<small>Yesterday at 07:58:35 PM</small></div>
<div class="abs list-item" style="left:110px;top:912px">Praesent luptatum delenit augue duis dolore<small>Yesterday at 07:11:19 PM</small></div>

<div class="abs list-title" style="left:356px">Events</div>
<div class="abs list-item" style="left:357px;top:846px">Praesent luptatum delenit augue duis dolore<small>Yesterday at 08:23:14 PM</small></div>
<div class="abs list-item" style="left:357px;top:878px">Praesent luptatum delenit augue duis dolore<small>Yesterday at 07:58:35 PM</small></div>
<div class="abs list-item" style="left:357px;top:912px">Praesent luptatum delenit augue duis dolore<small>Yesterday at 07:11:19 PM</small></div>

<div class="abs list-title" style="left:588px">News</div>
<div class="abs news-thumb" style="top:844px" role="img" aria-label="Author portrait"></div>
<div class="abs news-name" style="top:842px">Dana Whitfield</div>
<div class="abs news-text" style="top:859px">On sait depuis longtemps que travailler avec du texte lisible</div>
<div class="abs news-date" style="top:871px">14-12-2012</div>
<div class="abs news-thumb" style="top:903px" role="img" aria-label="Author portrait"></div>
<div class="abs news-name" style="top:902px">Dana Whitfield</div>
<div class="abs news-text" style="top:918px">On sait depuis longtemps que travailler avec du texte lisible</div>
<div class="abs news-date" style="top:930px">14-12-2012</div>

<!-- footer -->
<div class="abs footer"></div>
<div class="abs footer-title" style="left:96px">Contact Details</div>
<div class="abs footer-text" style="left:96px;top:1027px">1264 Some Building, Street<br>City, Postal Code</div>
<div class="abs footer-text" style="left:96px;top:1066px">Phone No. : 00 123 254-1234</div>
<div class="abs footer-text" style="left:96px;top:1092px">E-mail : support@phovan.org</div>

<div class="abs footer-title" style="left:299px">SiteMap</div>
<div class="abs footer-text lines" style="left:299px;top:1025px">Lorem Ipsum is simplement<br>Dignissim qui blandit praesent<br>Eleend oon congue imperdie<br>Claritas process dynamicus<br>Laoreet dolore magna aliquam</div>

<div class="abs footer-title" style="left:482px">Testimonials</div>
<div class="abs footer-text" style="left:484px;top:1027px">Lorem Ipsum est simplement du<br>fauxtexte employé.<br><em>Dana Whitfield</em></div>
<div class="abs footer-text" style="left:484px;top:1082px">Lorem Ipsum est simplement du<br>fauxtexte employé.<br><em>Anonymous</em></div>

<div class="abs footer-title" style="left:681px">Inspector Login</div>
<div class="abs field" style="top:1029px">username</div>
<div class="abs field" style="top:1058px">password</div>
<div class="abs footer-text" style="left:686px;top:1086px">Forgot your password</div>
<div class="abs login-btn">Log in</div>

<div class="abs bottom-bar">
  <span class="abs" style="left:11px">Copyright 2012. Company Name, All Rights Reserved.</span>
  <span class="abs" style="left:454px">Home</span>
  <span class="abs" style="left:506px">Find an Inspector</span>
  <span class="abs" style="left:610px">Ask PHOVAN</span>
  <span class="abs" style="left:680px">Conferences</span>
</div>

</body>
</html>
```